Brightbay Orthodontics business card design

Need a business card design that reflects our re-branding (orthodontic office - braces) and a new partnership with a pediatric dental office. We would like to include "for adults and children" on the card as well so adults know they are welcome to get their braces here as well. Office design is modern and would like business card to reflect a modern type look. Here's the text we would like to be included on the card:

Darren Wolcott, DDS, MSD
5214 West Linden Avenue, Suite 204
Mansfield, TX 76991
555-418-2637
www.brightbayortho.example
info@brightbayortho.example

Can we add the following to the existing designs? Darren Wolcott, DDS, MSD 5214 West Linden Avenue, Suite 204 Mansfield, TX 76991 555-418-2637

Does anyone have any more vertical designs available? Thanks!

Dental

```html
<!DOCTYPE html>
<html lang="en">
<head>
<meta charset="utf-8">
<title>Brightbay Orthodontics – Business Card</title>
<link href="https://fonts.googleapis.com/css2?family=Open+Sans:wght@400;600;700&display=swap" rel="stylesheet">
<style>
  :root {
    --bg: #e6e6e6;
    --card: #ffffff;
    --ink: #4a4a4a;
    --ink-soft: #6a6a6a;
    --brand-grey: #6f6f6f;
    --name-blue: #7f9fcf;
    --blue: #3f6bb0;
    --arc-blue: #8f9fd6;
    --pink: #e0389a;
    --orange: #ef8a3a;
    --green: #8cc45a;
  }
  * { box-sizing: border-box; margin: 0; padding: 0; }
  html, body {
    width: 1200px; height: 753px; overflow: hidden;
    background: var(--bg);
    font-family: "Open Sans", Arial, sans-serif;
  }
  .sheet { position: relative; width: 1200px; height: 753px; }
  .card {
    position: absolute; top: 79px; width: 340px; height: 595px;
    background: var(--card);
    box-shadow: 0 6px 18px rgba(0,0,0,.12);
    overflow: hidden;
  }
  .card--front { left: 230px; }
  .card--back { left: 630px; }

  /* Front */
  .front-brand {
    position: absolute; left: 50%; top: 50%;
    transform: translate(-50%, -50%) rotate(90deg);
    display: flex; align-items: center; gap: 14px;
    white-space: nowrap;
  }
  .brand-dot { width: 34px; height: 34px; border-radius: 50%; background: var(--arc-blue); flex: none; }
  .front-brand .brand-name {
    font-size: 40px; font-weight: 700; color: var(--brand-grey); letter-spacing: .5px;
  }

  /* Back */
  .back-graphics { position: absolute; inset: 0; }
  .back-brand {
    position: absolute; left: 28px; top: 46px;
    display: flex; align-items: flex-start; gap: 10px;
  }
  .back-brand .brand-dot { width: 26px; height: 26px; margin-top: 10px; }
  .back-brand .brand-name { font-size: 22px; font-weight: 700; color: var(--brand-grey); line-height: 1.1; }
  .tagline {
    margin-top: 6px;
    font-size: 11px; font-weight: 600; color: var(--name-blue); letter-spacing: .3px;
  }
  .doctor { position: absolute; left: 28px; top: 248px; }
  .doctor-name { font-size: 17px; font-weight: 400; color: var(--name-blue); }
  .doctor-title { font-size: 11px; color: var(--ink-soft); margin-top: 2px; }
  .address {
    position: absolute; left: 28px; top: 360px;
    font-size: 12px; line-height: 1.5; color: var(--ink-soft); font-style: normal;
  }
  .contacts {
    position: absolute; left: 28px; top: 418px; list-style: none;
    font-size: 12px; line-height: 1.55; color: var(--ink);
  }
  .contacts li { display: flex; align-items: center; gap: 8px; }
  .contacts svg { width: 10px; height: 10px; fill: var(--ink-soft); flex: none; }
</style>
</head>
<body>
<main class="sheet">
  <section class="card card--front" aria-label="Card front">
    <div class="front-brand">
      <span class="brand-dot"></span>
      <span class="brand-name">Brightbay Orthodontics</span>
    </div>
  </section>

  <section class="card card--back" aria-label="Card back">
    <svg class="back-graphics" viewBox="0 0 340 595" aria-hidden="true">
      <path d="M0 232 Q170 215 340 110" fill="none" stroke="var(--arc-blue)" stroke-width="2"/>
      <path d="M0 240 Q180 222 340 120" fill="none" stroke="var(--pink)" stroke-width="2.5"/>
      <path d="M340 382 C300 420 260 470 225 530 C210 560 195 580 180 595 L340 595 Z" fill="var(--blue)"/>
      <path d="M340 372 C290 410 250 470 215 530 C200 560 185 580 168 595" fill="none" stroke="var(--pink)" stroke-width="4"/>
      <path d="M0 565 C90 560 150 545 205 515" fill="none" stroke="var(--orange)" stroke-width="5"/>
      <path d="M0 582 C70 580 110 575 150 562" fill="none" stroke="var(--green)" stroke-width="6"/>
    </svg>

    <div class="back-brand">
      <span class="brand-dot"></span>
      <div>
        <p class="brand-name">Brightbay<br>Orthodontics</p>
        <p class="tagline">for adults and children</p>
      </div>
    </div>

    <div class="doctor">
      <p class="doctor-name">Darren Wolcott</p>
      <p class="doctor-title">DDS, MSD</p>
    </div>

    <address class="address">
      5214 West Linden Avenue<br>
      Suite 204, Mansfield, TX 76991
    </address>

    <ul class="contacts">
      <li>
        <svg viewBox="0 0 10 10"><path d="M2 0.5 L3.8 2.6 L2.8 3.8 Q4 6 6.2 7.2 L7.4 6.2 L9.5 8 L8.3 9.5 Q3.5 9 0.5 1.7 Z"/></svg>
        555-418-2637
      </li>
      <li>
        <svg viewBox="0 0 10 10"><circle cx="5" cy="5" r="4.3" fill="none" stroke="#6a6a6a" stroke-width="1"/><path d="M0.7 5 H9.3 M5 0.7 V9.3" stroke="#6a6a6a" stroke-width="0.9"/><ellipse cx="5" cy="5" rx="2" ry="4.3" fill="none" stroke="#6a6a6a" stroke-width="0.9"/></svg>
        www.brightbayortho.example
      </li>
      <li>
        <svg viewBox="0 0 10 10"><rect x="0.5" y="2" width="9" height="6.5" fill="none" stroke="#6a6a6a" stroke-width="1"/><path d="M0.5 2 L5 5.8 L9.5 2" fill="none" stroke="#6a6a6a" stroke-width="1"/></svg>
        info@brightbayortho.example
      </li>
    </ul>
  </section>
</main>
</body>
</html>
```